Front page of Orthodox Christian Monastery Website

I am attaching a couple of versions of design that was already created for the front page of the website. You can grab the same pictures and titles (do not need to know the Russian language) to create your own version of design.
Background: Monastery website contains sermons, stories about monastery life, monastery music of the sisterhood.
Main principles of the design:
1. Various materials/sermons/music have to be clearly visible immediately to the site visitor.
2. Text descriptions to photos should be using font with a good contrast, highly clickable and easily readable.
3. Every article should have a photo or a quality picture (use those in the sample) that will convey something about it.
4. On the top, there will be a menu, which will be a line of words (just use generic words for now).
5. Design should reflect Christian Orthodox themes and fonts.
Updates

Target Market(s)

Orthodox Christian believers around the world and those that are interested in Orthodox Christianity

Number of Pages Required

1 page

Font styles to use
Serif

Colors

Designer to choose colors to be used in the design.

Requirements
Must have
• In the project description
Nice to have
• for some ideas see a popular Orthodox Christian website:
• www.verenskaya-lampada.ru
• We don't want to copy it, but it could give ideas.
Should not have
• Should not be overly complex

```html
<!DOCTYPE html>
<html lang="en">
<head>
<meta charset="utf-8">
<title>Orthodox Christian Monastery</title>
<link rel="stylesheet" href="https://fonts.googleapis.com/css2?family=Domine:wght@400;700&family=Open+Sans:wght@400;600;700&display=swap">
<style>
:root{
  --green:#1f6b14;
  --green-dark:#0f3a0c;
  --green-band:#237a1c;
  --red:#7d0f12;
  --red-soft:#9a2e33;
  --text:#555;
  --title:#2a6e12;
  --line:#d9d9d9;
  --white:#fff;
  --sky-top:#6f9fd6;
  --sky-mid:#c9dcef;
}
*{box-sizing:border-box;margin:0;padding:0}
html,body{width:1200px;height:2571px;overflow:hidden}
body{position:relative;background:var(--white);font-family:"Open Sans",Arial,sans-serif;color:var(--text)}
.abs{position:absolute}
.top-bg{left:0;top:0;width:1200px;height:700px;background:linear-gradient(180deg,var(--sky-top) 0%,#a9c6e6 40%,var(--sky-mid) 70%,#fff 100%)}
.brand{left:194px;top:28px;font-family:"Domine",Georgia,serif;font-weight:700;font-size:27px;line-height:28px;color:var(--green);letter-spacing:.5px}
.search{left:715px;top:43px;width:285px;height:34px;background:#f2f2f2;display:flex;align-items:center;padding-left:14px;gap:10px;font-size:10px;color:#999;text-transform:uppercase}
.nav{left:192px;top:103px;width:816px;height:46px;background:var(--green);display:flex}
.nav a{color:#fff;text-decoration:none;font-size:13.5px;font-weight:600;display:flex;align-items:center;padding:0 24px;height:46px}
.nav a.active{background:var(--red);width:123px;justify-content:center}
.ph{display:block}
.hero-main{left:192px;top:149px;width:523px;height:360px;background:linear-gradient(180deg,#5d8fd0 0%,#8fb4e0 45%,#6a6a55 80%,#3b3a30 100%)}
.hero-cap{left:221px;color:#fff;font-size:16px;text-transform:uppercase;letter-spacing:.3px}
.hero-tile{left:716px;width:292px;height:180px}
.tile-a{top:149px;background:radial-gradient(circle at 40% 40%,#e0a050,#8a3a14 60%,#3a160a)}
.tile-b{top:329px;background:linear-gradient(135deg,#2b3f8a,#8a2020 50%,#2e5a3a)}
.tile-cap{left:736px;color:#fff;font-size:14.5px;text-transform:uppercase}
.tile-sub{left:736px;color:#fff;font-size:11.5px;text-transform:uppercase}
.arrows{left:667px;top:474px;display:flex;gap:4px}
.arrows span{width:17px;height:17px;border-radius:50%;background:#fff;display:flex;align-items:center;justify-content:center}
.h2{font-family:"Domine",Georgia,serif;font-size:26px;color:#222;text-transform:uppercase}
.dbl{height:5px;border-top:1px solid #888;border-bottom:1px solid #888}
.card{background:#fff;border:1px solid var(--line);box-shadow:0 1px 3px rgba(0,0,0,.08)}
.card .img{height:170px}
.card h3{font-family:"Open Sans",sans-serif;font-weight:400;font-size:15px;color:var(--title);margin:14px 0 6px 24px;text-transform:uppercase}
.card p{font-size:10.5px;line-height:14px;margin:0 24px;color:#777}
.more{display:inline-block;font-size:10.5px;font-weight:700;color:var(--red);text-transform:uppercase;margin:12px 0 0 24px}
.band{left:0;top:880px}
.stories-h{left:197px;top:988px;color:#fff;font-family:"Domine",Georgia,serif;font-size:24px}
.story{background:#fff}
.story .img{height:132px}
.story h3{font-size:13px;font-weight:400;color:#333;margin:12px 0 4px 22px;text-transform:uppercase}
.story p{font-size:9.5px;line-height:12px;margin:0 18px 0 22px;color:#666}
.story .more{margin:10px 0 0 22px;font-size:9.5px}
.music-h{left:192px;top:1485px;font-family:"Domine",Georgia,serif;font-size:24px;line-height:32px;color:#222;text-transform:uppercase}
.item-img{left:192px;width:197px;height:130px}
.item-title{left:406px;font-size:15.5px;font-weight:600;color:var(--title)}
.item-text{left:406px;width:330px;font-size:11.5px;line-height:17px;color:#555}
.item-more{left:406px;font-size:11.5px;font-weight:700;color:var(--red);text-transform:uppercase}
.sep{left:192px;width:533px;height:1px;background:var(--line)}
.life{left:759px;top:1490px;width:249px;height:821px;border:1px solid var(--line);background:#fff}
.life-h{height:48px;background:var(--red-soft);color:#fff;font-family:"Domine",Georgia,serif;font-size:20px;padding:12px 0 0 26px}
.blog{position:absolute;left:20px;width:207px}
.blog .img{height:89px}
.blog h4{font-size:12.5px;font-weight:600;color:var(--title);margin:10px 0 4px}
.blog p{font-size:10px;line-height:13px;color:#666}
.blog .more{margin:4px 0 0;font-size:9.5px}
.footer{left:0;top:2310px}
.foot-nav{left:0;top:2430px;width:1200px;display:flex;justify-content:center;gap:34px}
.foot-nav a{color:#fff;text-decoration:none;font-size:13px;font-weight:600}
.copy{left:0;top:2461px;width:1200px;text-align:center;color:#b8c8b4;font-size:10.5px}
</style>
</head>
<body>
<div class="abs top-bg"></div>

<header>
  <div class="abs brand">ORTHODOX CHRISTIAN<br>MONASTERY</div>
  <div class="abs search">
    <svg width="13" height="13" viewBox="0 0 13 13"><circle cx="5.5" cy="5.5" r="4.2" fill="none" stroke="#777" stroke-width="1.6"/><line x1="8.6" y1="8.6" x2="12" y2="12" stroke="#777" stroke-width="1.8"/></svg>
    <span>Enter keyword</span>
  </div>
  <nav class="abs nav">
    <a class="active" href="#">HOME</a><a href="#">ABOUT US</a><a href="#">OUR BLOGS</a><a href="#">ARTICLES</a><a href="#">SERMONS</a><a href="#">LIFE</a><a href="#">CONTACT</a>
  </nav>
</header>

<section class="hero">
  <div class="abs ph hero-main" role="img" aria-label="White church with dark onion dome against blue sky"></div>
  <div class="abs hero-cap" style="top:443px">Morbi diam mauris viverra in gravida</div>
  <div class="abs hero-cap" style="top:466px;font-size:14px">Eu mattis in ante morbi eget arcu</div>
  <div class="abs arrows">
    <span><svg width="7" height="9" viewBox="0 0 7 9"><path d="M5 1L2 4.5L5 8" fill="none" stroke="#333" stroke-width="1.5"/></svg></span>
    <span><svg width="7" height="9" viewBox="0 0 7 9"><path d="M2 1L5 4.5L2 8" fill="none" stroke="#333" stroke-width="1.5"/></svg></span>
  </div>
  <div class="abs ph hero-tile tile-a" role="img" aria-label="Wooden cross in warm candle light"></div>
  <div class="abs tile-cap" style="top:282px">Maecenas at justo id velit</div>
  <div class="abs tile-sub" style="top:302px">Donec dictum lectus</div>
  <div class="abs ph hero-tile tile-b" role="img" aria-label="Stained glass window with saints"></div>
  <div class="abs tile-cap" style="top:456px">Curabitur iaculis tempus</div>
  <div class="abs tile-sub" style="top:476px">Curabitur vel mi sit amet</div>
</section>

<section class="sermons">
  <div class="abs h2" style="left:0;width:1200px;text-align:center;top:548px">Sermons</div>
  <div class="abs dbl" style="left:566px;top:586px;width:66px"></div>
  <article class="abs card" style="left:190px;top:605px;width:264px;height:278px">
    <div class="img ph" role="img" aria-label="Priest writing with an inkwell" style="background:linear-gradient(90deg,#c8c8c8,#6d6d6d 50%,#2f5a2a)"></div>
    <h3>Article title here</h3><p>Proin nulla arcu nonummy luctus dictum eget fermentum et lorema</p><span class="more">Read more ›</span>
  </article>
  <article class="abs card" style="left:468px;top:605px;width:264px;height:278px">
    <div class="img ph" role="img" aria-label="Nun speaking at a lectern on stage" style="background:linear-gradient(180deg,#14147a,#2530b0 60%,#10104a)"></div>
    <h3>Article title here</h3><p>Proin nulla arcu nonummy luctus dictum eget fermentum et lorema</p><span class="more">Read more ›</span>
  </article>
  <article class="abs card" style="left:746px;top:605px;width:264px;height:278px">
    <div class="img ph" role="img" aria-label="Two nuns in black habits" style="background:linear-gradient(90deg,#d8dce4,#2a2a2a 30%,#bfb8b0 50%,#1f1f1f 80%)"></div>
    <h3>Article title here</h3><p>Proin nulla arcu nonummy luctus dictum eget fermentum et lorema</p><span class="more">Read more ›</span>
  </article>
</section>

<section class="stories">
  <svg class="abs band" width="1200" height="570" viewBox="0 0 1200 570">
    <polygon points="1200,25 880,80 1200,110" fill="#c47a7a"/>
    <polygon points="0,10 1200,80 1200,560 0,460" fill="var(--green-band)"/>
    <polygon points="880,80 1200,50 1200,113" fill="var(--red)"/>
    <polygon points="0,460 260,470 0,512" fill="var(--red)"/>
  </svg>
  <div class="abs stories-h">STORIES ABOUT MONASTERY</div>
  <div class="abs dbl" style="left:197px;top:1024px;width:66px;border-color:#cfe3c8"></div>
  <article class="abs story" style="left:195px;top:1054px;width:192px;height:243px">
    <div class="img ph" role="img" aria-label="Nuns carrying red flowers" style="background:linear-gradient(135deg,#3a3a3a,#7a6a60 50%,#b0203a)"></div>
    <h3>Story title</h3><p>Class aptent taciti sociosqu ad litora torquent per conubia nostra per inceptos hymenaeos Proin</p><span class="more">Read more ›</span>
  </article>
  <article class="abs story" style="left:403px;top:1054px;width:190px;height:243px">
    <div class="img ph" role="img" aria-label="Ornate red and gold church interior" style="background:linear-gradient(90deg,#8a4a2a,#d8a080 50%,#7a2a1a)"></div>
    <h3>Story title</h3><p>Class aptent taciti sociosqu ad litora torquent per conubia nostra per inceptos hymenaeos Proin</p><span class="more">Read more ›</span>
  </article>
  <article class="abs story" style="left:607px;top:1054px;width:192px;height:243px">
    <div class="img ph" role="img" aria-label="Sermon announcement with a priest" style="background:linear-gradient(135deg,#1a1a1a,#6a5a4a 60%,#c0b090)"></div>
    <h3>Story title</h3><p>Class aptent taciti sociosqu ad litora torquent per conubia nostra per inceptos hymenaeos Proin</p><span class="more">Read more ›</span>
  </article>
  <article class="abs story" style="left:813px;top:1054px;width:192px;height:243px">
    <div class="img ph" role="img" aria-label="Colourful painted icon" style="background:radial-gradient(circle,#3a8aa0,#b04030 60%,#3a2a6a)"></div>
    <h3>Story title</h3><p>Class aptent taciti sociosqu ad litora torquent per conubia nostra per inceptos hymenaeos Proin</p><span class="more">Read more ›</span>
  </article>
</section>

<section class="music">
  <div class="abs music-h">Monastery music of<br>the sisterhood</div>
  <div class="abs dbl" style="left:192px;top:1556px;width:66px;border-color:#6a9a60"></div>

  <div class="abs ph item-img" style="top:1586px;background:linear-gradient(180deg,#1a1a22,#3a3a48)" role="img" aria-label="Choir concert poster"></div>
  <div class="abs item-title" style="top:1584px">Integer congue augue et malesuada</div>
  <div class="abs item-text" style="top:1611px">Mauris vel lacus vitae felis vestibulum volutpat Etiam est nunc venenatis in tristique eu imperdiet ac nisl Cum sociis natoque penatibus et magnis dis parturient montes nascetur ridiculus mus In iaculis facilisis massa Etiam eu</div>
  <div class="abs item-more" style="top:1693px">Read more</div>
  <div class="abs sep" style="top:1740px"></div>

  <div class="abs ph item-img" style="top:1772px;background:linear-gradient(135deg,#1a3a8a,#b03020 45%,#d8a030 70%,#2a5a30)" role="img" aria-label="Stained glass of saints"></div>
  <div class="abs item-title" style="top:1770px">Donec dictum lectus non odio</div>
  <div class="abs item-text" style="top:1797px">Mauris vel lacus vitae felis vestibulum volutpat Etiam est nunc venenatis in tristique eu imperdiet ac nisl Cum sociis natoque penatibus et magnis dis parturient montes nascetur ridiculus mus In iaculis facilisis massa Etiam eu</div>
  <div class="abs item-more" style="top:1879px">Read more</div>
  <div class="abs sep" style="top:1928px"></div>

  <div class="abs ph item-img" style="top:1965px;background:linear-gradient(135deg,#e8c8a0,#c87a6a 50%,#8aa0c0)" role="img" aria-label="Painting of angels with harps"></div>
  <div class="abs item-title" style="top:1963px">Pellentesque faucibus Ut accum</div>
  <div class="abs item-text" style="top:1990px">Mauris vel lacus vitae felis vestibulum volutpat Etiam est nunc venenatis in tristique eu imperdiet ac nisl Cum sociis natoque penatibus et magnis dis parturient montes nascetur ridiculus mus In iaculis facilisis massa Etiam eu</div>
  <div class="abs item-more" style="top:2072px">Read more</div>
  <div class="abs sep" style="top:2123px"></div>

  <div class="abs ph item-img" style="top:2157px;background:linear-gradient(180deg,#3a2418,#7a5040 60%,#2a1a12)" role="img" aria-label="Sisterhood choir singing"></div>
  <div class="abs item-title" style="top:2155px">Aenean porttitor eros vel dolor Donec</div>
  <div class="abs item-text" style="top:2182px">Mauris vel lacus vitae felis vestibulum volutpat Etiam est nunc venenatis in tristique eu imperdiet ac nisl Cum sociis natoque penatibus et magnis dis parturient montes nascetur ridiculus mus In iaculis facilisis massa Etiam eu</div>
  <div class="abs item-more" style="top:2264px">Read more</div>
</section>

<aside class="abs life">
  <div class="life-h">LIFE</div>
  <div class="blog" style="top:70px"><div class="img ph" role="img" aria-label="Hands in prayer in dim light" style="background:linear-gradient(135deg,#1a1a1a,#6a4a30 60%,#1a1a1a)"></div><h4>Blog Title here</h4><p>Class aptent taciti sociosqu ad litora torquent per conubia nostra per</p><span class="more">Read more</span></div>
  <div class="blog" style="top:256px"><div class="img ph" role="img" aria-label="Open book in warm light" style="background:linear-gradient(135deg,#3a2a1a,#e0c8a0 55%,#6a4a2a)"></div><h4>Blog Title here</h4><p>Class aptent taciti sociosqu ad litora torquent per conubia nostra per</p><span class="more">Read more</span></div>
  <div class="blog" style="top:442px"><div class="img ph" role="img" aria-label="Person praying in soft light" style="background:linear-gradient(90deg,#2a1a12,#a07050 50%,#f0e8e0)"></div><h4>Blog Title here</h4><p>Class aptent taciti sociosqu ad litora torquent per conubia nostra per</p><span class="more">Read more</span></div>
  <div class="blog" style="top:628px"><div class="img ph" role="img" aria-label="Lit candle in darkness" style="background:radial-gradient(circle at 40% 50%,#f0d8b0,#6a4a30 35%,#1a1410)"></div><h4>Blog Title here</h4><p>Class aptent taciti sociosqu ad litora torquent per conubia nostra per</p><span class="more">Read more</span></div>
</aside>

<footer>
  <svg class="abs footer" width="1200" height="261" viewBox="0 0 1200 261">
    <path d="M0,22 Q600,-20 1200,22 L1200,261 L0,261 Z" fill="var(--green-dark)"/>
  </svg>
  <nav class="abs foot-nav"><a href="#">HOME</a><a href="#">ABOUT US</a><a href="#">OUR BLOGS</a><a href="#">ARTICLES</a><a href="#">SERMONS</a><a href="#">LIFE</a><a href="#">CONTACT</a></nav>
  <div class="abs copy">© 2018 Company Name &nbsp;All right reserved</div>
</footer>
</body>
</html>
```